Business Card Design for Training Business

Clear Path Coaching is a new business that delivers training and other services with a focus on topics related to mental health and wellbeing, for example, Wellmind Response Course, Resilience etc. We have a strong focus on evidence-based psychology and neuroscience. I have a logo which I will upload with the brief, so please consider colours that work well with the logo.
Target Market(s)
Adults, workplaces (particularly government and not-for-profits)
Industry/Entity Type
Business
Contact Information for Business Card
Head Strong TrainingSamantha SellwoodDirector0438 770 850sam@headstrongtraining.com.auwww.headstrongtraining.com.au

```html
<!DOCTYPE html>
<html lang="en">
<head>
<meta charset="utf-8">
<title>Clear Path Coaching — Business Card</title>
<link rel="stylesheet" href="https://fonts.googleapis.com/css2?family=Questrial&display=swap">
<style>
  :root {
    --backdrop: #2f2f2f;
    --card: #f7f7f7;
    --teal: #2bb5bd;
    --teal-soft: #9fd6cf;
    --ink: #5b5654;
    --ink-dark: #3f3b3a;
  }
  * { margin: 0; padding: 0; box-sizing: border-box; }
  html, body { width: 1200px; height: 750px; overflow: hidden; }
  body {
    background: var(--backdrop);
    font-family: "Questrial", "Century Gothic", sans-serif;
    position: relative;
  }
  .card-pair {
    position: absolute;
    left: 136px;
    top: 244px;
    display: flex;
    gap: 5px;
  }
  .card {
    position: relative;
    width: 461px;
    height: 262px;
    background: var(--card);
    overflow: hidden;
  }
  .wordmark { color: var(--ink); text-align: center; }
  .wordmark-name {
    font-size: 24px;
    letter-spacing: 2.5px;
    line-height: 1;
    white-space: nowrap;
  }
  .wordmark-tag {
    font-size: 11px;
    letter-spacing: 5.5px;
    margin-top: 9px;
    color: var(--ink-dark);
  }
  .front .wordmark { position: absolute; left: 40px; top: 50px; }
  .front .wordmark-name { font-size: 24px; }
  .person { position: absolute; left: 41px; top: 116px; }
  .person-name { font-size: 18px; color: var(--teal); line-height: 1.1; }
  .person-role { font-size: 13px; color: var(--ink-dark); margin-top: 2px; }
  .contacts { position: absolute; left: 42px; top: 167px; list-style: none; }
  .contacts li {
    display: flex;
    align-items: center;
    gap: 7px;
    font-size: 12px;
    color: var(--ink);
    height: 18px;
  }
  .contacts svg { width: 12px; height: 12px; flex: none; }
  .pattern-half {
    position: absolute;
    top: -2px;
    width: 134px;
    height: 266px;
  }
  .front .pattern-half { right: 0; }
  .back .pattern-half { left: 0; }
  .back .brand {
    position: absolute;
    left: 0; right: 0;
    top: 80px;
    display: flex;
    flex-direction: column;
    align-items: center;
  }
  .brand-dot {
    width: 56px; height: 56px;
    border-radius: 50%;
    border: 2px solid var(--teal);
    margin-bottom: 14px;
  }
  .back .wordmark-name { font-size: 19px; letter-spacing: 2px; }
  .back .wordmark-tag { font-size: 9px; letter-spacing: 4.5px; margin-top: 6px; }
</style>
</head>
<body>
  <main class="card-pair">
    <section class="card front">
      <div class="wordmark">
        <div class="wordmark-name">CLEAR PATH</div>
        <div class="wordmark-tag">COACHING</div>
      </div>
      <div class="person">
        <div class="person-name">Rebecca Tanfield</div>
        <div class="person-role">Director</div>
      </div>
      <ul class="contacts">
        <li>
          <svg viewBox="0 0 12 12"><path d="M2.5 1 L4.5 1 L5.2 3.6 L3.9 4.6 Q5 7 7.4 8.1 L8.4 6.8 L11 7.5 L11 9.5 Q10.5 11 9 11 Q1 10 1 2.8 Q1 1.3 2.5 1 Z" fill="var(--teal)"/></svg>
          0491 362 517
        </li>
        <li>
          <svg viewBox="0 0 12 12"><rect x="0.5" y="2.5" width="11" height="7.5" fill="var(--teal)"/><path d="M0.8 2.8 L6 7 L11.2 2.8" stroke="#fff" stroke-width="1" fill="none"/></svg>
          bec@clearpathcoaching.example.au
        </li>
        <li>
          <svg viewBox="0 0 12 12"><circle cx="6" cy="6" r="5.5" fill="var(--teal)"/><path d="M3 3.5 Q5 4 4.5 6 Q6.5 7 5.5 9.5 M7.5 2 Q7 4 9 4.5" stroke="#fff" stroke-width="1" fill="none"/></svg>
          www.clearpathcoaching.example.au
        </li>
      </ul>
      <svg class="pattern-half" viewBox="0 0 134 266" role="img" aria-label="Decorative geometric circular pattern in teal, left half">
        <defs>
          <radialGradient id="halfGlowLeft" cx="134" cy="133" r="133" gradientUnits="userSpaceOnUse">
            <stop offset="0" stop-color="#ffffff"/>
            <stop offset="0.55" stop-color="var(--teal-soft)" stop-opacity="0.55"/>
            <stop offset="1" stop-color="var(--teal)" stop-opacity="0.75"/>
          </radialGradient>
        </defs>
        <path d="M134 0 A133 133 0 0 0 134 266 Z" fill="url(#halfGlowLeft)"/>
      </svg>
    </section>

    <section class="card back">
      <svg class="pattern-half" viewBox="0 0 134 266" role="img" aria-label="Decorative geometric circular pattern in teal, right half">
        <defs>
          <radialGradient id="halfGlowRight" cx="0" cy="133" r="133" gradientUnits="userSpaceOnUse">
            <stop offset="0" stop-color="#ffffff"/>
            <stop offset="0.55" stop-color="var(--teal-soft)" stop-opacity="0.55"/>
            <stop offset="1" stop-color="var(--teal)" stop-opacity="0.75"/>
          </radialGradient>
        </defs>
        <path d="M0 0 A133 133 0 0 1 0 266 Z" fill="url(#halfGlowRight)"/>
      </svg>
      <div class="brand">
        <div class="brand-dot"></div>
        <div class="wordmark">
          <div class="wordmark-name">CLEAR PATH</div>
          <div class="wordmark-tag">COACHING</div>
        </div>
      </div>
    </section>
  </main>
</body>
</html>
```